Business cards to launch an education platform

Hi,
I am looking at having new business cards designed.
I am a startup, developing a web platform for schools and university, the education world. It's an online assessment system.
I would like a card that looks classy, and that is using the colors and the font of my logo.

I have attached:
1) my logo
2) A business card that I have designed quickly so you can have all the information required in the card, but I really don't like it.
3) The font that I am using (Lato Regular) to design my web platform
4) Some screenshots of my web platform so you can have a look at the style that I have.

Target Market(s)

Major market: Education system: Schools and university
Minor markets: Business in general

Industry/Entity Type

Business

Contact Information for Business Card

Clara Fenwick
Director

M: 0437 518 902
E: clara.fenwick@amberLoomSystems.com.au

Requirements
Must have
• The colors of my logo

```html
<!DOCTYPE html>
<html lang="en">
<head>
<meta charset="utf-8">
<title>Amber Loom Systems – Business Cards</title>
<link rel="stylesheet" href="https://fonts.googleapis.com/css2?family=Lato:wght@400;700&family=Arimo:wght@400;700&display=swap">
<style>
  :root {
    --page-bg: #e9e6e1;
    --navy: #1d4f80;
    --navy-deep: #123c66;
    --stripe: #0f4a78;
    --cyan: #15c6e3;
    --blue-band-end: #1273c6;
    --paper: #fbfbfb;
    --ink-brand: #1e4f7a;
    --white: #ffffff;
  }
  * { box-sizing: border-box; margin: 0; padding: 0; }
  html, body { width: 1200px; height: 902px; overflow: hidden; }
  body {
    background: var(--page-bg);
    position: relative;
    font-family: "Lato", sans-serif;
  }
  .card {
    position: absolute;
    top: 292px;
    width: 520px;
    height: 318px;
    border-radius: 4px;
    overflow: hidden;
    box-shadow: 0 8px 24px rgba(0,0,0,0.18);
  }
  /* Back of card */
  .card--back {
    left: 50px;
    background: linear-gradient(160deg, var(--navy) 0%, var(--navy-deep) 100%);
    display: flex;
    align-items: center;
    justify-content: center;
    gap: 22px;
  }
  .brand-mark {
    width: 64px;
    height: 64px;
    background: var(--white);
    flex: none;
  }
  .brand-name {
    font-family: "Lato", sans-serif;
    font-weight: 400;
    font-size: 40px;
    letter-spacing: 3px;
    line-height: 1.1;
    color: var(--white);
  }
  /* Front of card */
  .card--front {
    left: 630px;
    background: var(--paper);
  }
  .front-brand {
    position: absolute;
    top: 62px;
    left: 0;
    right: 0;
    display: flex;
    align-items: center;
    justify-content: center;
    gap: 20px;
  }
  .front-brand .brand-mark { background: var(--ink-brand); width: 56px; height: 56px; }
  .front-brand .brand-name { color: var(--ink-brand); font-size: 34px; }
  .stripe {
    position: absolute;
    left: 0; right: 0;
    top: 176px;
    height: 16px;
    background: var(--stripe);
  }
  .contact-band {
    position: absolute;
    left: 0; right: 0;
    top: 192px;
    bottom: 0;
    background: linear-gradient(100deg, var(--cyan) 0%, #10a6da 55%, var(--blue-band-end) 100%);
    display: flex;
    align-items: center;
    padding: 0 22px;
    color: var(--white);
    font-family: "Arimo", sans-serif;
  }
  .person { flex: none; width: 170px; }
  .person__name { font-weight: 700; font-size: 25px; line-height: 1.1; }
  .person__role { font-size: 17px; margin-top: 4px; }
  .divider {
    width: 1.5px;
    align-self: stretch;
    margin: 22px 14px 22px 0;
    background: rgba(255,255,255,0.85);
  }
  .details { list-style: none; display: flex; flex-direction: column; gap: 10px; }
  .details li { display: flex; align-items: center; gap: 8px; font-size: 13.5px; white-space: nowrap; }
  .details .phone { font-size: 17px; }
  .icon { width: 18px; height: 18px; flex: none; }
</style>
</head>
<body>

  <section class="card card--back" aria-label="Business card back">
    <span class="brand-mark"></span>
    <span class="brand-name">AMBER LOOM<br>SYSTEMS</span>
  </section>

  <section class="card card--front" aria-label="Business card front">
    <div class="front-brand">
      <span class="brand-mark"></span>
      <span class="brand-name">AMBER LOOM<br>SYSTEMS</span>
    </div>
    <div class="stripe"></div>
    <div class="contact-band">
      <div class="person">
        <p class="person__name">Clara Fenwick</p>
        <p class="person__role">Director</p>
      </div>
      <span class="divider"></span>
      <ul class="details">
        <li class="phone">
          <svg class="icon" viewBox="0 0 18 18" aria-hidden="true">
            <rect x="0.5" y="0.5" width="17" height="17" rx="2" fill="#fff"/>
            <path d="M5 4.5c.6-.5 1.4-.4 1.7.2l.9 1.6c.3.5.1 1-.3 1.3l-.6.4c.5 1.2 1.4 2.1 2.6 2.6l.4-.6c.3-.4.9-.6 1.3-.3l1.6.9c.6.3.7 1.1.2 1.7l-.6.6c-.7.7-4 .2-6.2-2S3.7 5.8 4.4 5.1z" fill="#1273c6"/>
          </svg>
          0437 518 902
        </li>
        <li>
          <svg class="icon" viewBox="0 0 18 18" aria-hidden="true">
            <rect x="0.5" y="0.5" width="17" height="17" rx="2" fill="#fff"/>
            <rect x="3.5" y="5" width="11" height="8" fill="none" stroke="#1273c6" stroke-width="1.3"/>
            <path d="M3.5 5l5.5 4.5L14.5 5" fill="none" stroke="#1273c6" stroke-width="1.3"/>
          </svg>
          clara.fenwick@amberLoomSystems.com.au
        </li>
      </ul>
    </div>
  </section>

</body>
</html>
```